Upscale business cards needed for Board of Directors

We need professional business cards created for members of our family business Board of Directors. We would like these relatively simple and straightforward, but also with a unique element to set them apart. Probably stick with neutral and simple colors - white, grey etc. We need space for the traditional elements, including name, title, address, email/phone number. And we will be creating several from this template so it needs to be template that is easy to switch information in and out of.
Business
See description

```html
<!DOCTYPE html>
<html lang="en">
<head>
<meta charset="utf-8">
<title>Harborline Holdings – Business Card</title>
<link rel="stylesheet" href="https://fonts.googleapis.com/css2?family=Roboto:wght@400;500;700&display=swap">
<style>
  :root {
    --stage: #d9d9db;
    --card-white: #ffffff;
    --card-black: #141414;
    --ink: #1c1c1c;
    --ink-soft: #4a4a4a;
    --gold: #b39a6b;
    --rule-grey: #cfcfcf;
    --back-text: #f4f4f4;
    --back-muted: #9a9a9a;
  }
  * { box-sizing: border-box; margin: 0; padding: 0; }
  html, body {
    width: 1200px; height: 843px; overflow: hidden;
    background: var(--stage);
    font-family: "Roboto", Arial, sans-serif;
  }
  .canvas {
    width: 1200px; height: 843px;
    display: flex; align-items: center; justify-content: center; gap: 50px;
  }
  .card {
    position: relative;
    width: 525px; height: 300px;
    box-shadow: 0 10px 30px rgba(0,0,0,0.18);
  }
  .card--back { background: var(--card-black); }
  .card--front { background: var(--card-white); }

  .brand {
    position: absolute;
    display: flex; align-items: center; gap: 10px;
    font-weight: 700; white-space: nowrap; line-height: 1;
  }
  .brand__square { width: 12px; height: 12px; flex: none; }

  .card--back .brand {
    left: 0; right: 0; top: 128px; justify-content: center;
    font-size: 28px; color: var(--back-text);
  }
  .card--back .brand__square { width: 16px; height: 16px; background: var(--gold); }
  .card--back .back-url {
    position: absolute; left: 0; right: 0; bottom: 48px;
    text-align: center; color: var(--back-muted);
    font-size: 12px; font-weight: 700; letter-spacing: 3px;
  }

  .card--front .brand {
    left: 30px; width: 250px; top: 140px; justify-content: center;
    font-size: 20px; color: var(--ink);
  }
  .card--front .brand__square { background: var(--gold); }

  .divider {
    position: absolute; left: 290px; top: 50px; width: 3px; height: 205px;
    background: linear-gradient(to bottom, var(--gold) 0 22%, var(--rule-grey) 22% 100%);
  }
  .contact {
    position: absolute; left: 308px; top: 50px; right: 14px;
    color: var(--ink-soft);
  }
  .contact__name { font-size: 19px; font-weight: 500; color: var(--ink); letter-spacing: 0.6px; }
  .contact__title { font-size: 14px; color: var(--gold); margin-top: 3px; }
  .contact__lines { margin-top: 16px; font-size: 14px; line-height: 1.5; }
  .contact__label { font-weight: 700; color: var(--ink); }
  .contact__url {
    margin-top: 14px; font-size: 12.5px; font-weight: 700;
    letter-spacing: 2.4px; color: var(--ink);
  }
</style>
</head>
<body>
<main class="canvas">
  <section class="card card--back" aria-label="Card back">
    <div class="brand"><span class="brand__square"></span>Harborline Holdings</div>
    <p class="back-url">www.harborline.com</p>
  </section>

  <section class="card card--front" aria-label="Card front">
    <div class="brand"><span class="brand__square"></span>Harborline Holdings</div>
    <div class="divider"></div>
    <div class="contact">
      <p class="contact__name">MARK ELLISON</p>
      <p class="contact__title">President</p>
      <div class="contact__lines">
        <p>4127 Linden Court</p>
        <p>Maple Grove, NY 11020</p>
        <p><span class="contact__label">P:</span> 555 0142 7789</p>
        <p><span class="contact__label">E:</span> mark@harborline.com</p>
      </div>
      <p class="contact__url">www.harborline.com</p>
    </div>
  </section>
</main>
</body>
</html>
```